Halvik - consultancy website

I need a new design for my webpage/presence [to be functioning with Wordpress - I have a programmer to set it up but not the design idea].
My company is Halvik - a consultancy firm focused on growth management for Swedish SME's primarily;. We call it Leadership toolkit for firms on the rise, kind of a doctor helping small become big. Contentwise, its a simple frontpage + 3-4 subpages with content re company/myself/focus etc. The new site should communicate a fresh, trustworthy take yet simple and functional on all devices [i.e. think UI compatible for mobile/tablet]. Current building parts/form elements are
a) existing logo and text elements
b) existing pictures
c) the yellowish color
colours and new ideas on pictures/positioning are welcome. I prefer a 'full width page' solution with centralised text elements but that's all up to you to suggest. Current site is a quickfix made by myself - now I'm moving it to a new platform so want to take the opportunity to make it
Nothing superspecial as it is a 2-man show; on the other hand I still want to have a modern & fresh reflection of my brand in digital environments. Help me out!
www.halvik-demo.se
Best
Lina Bergqvist

```html
<!DOCTYPE html>
<html lang="en">
<head>
<meta charset="utf-8">
<title>Halvik – Why H</title>
<link rel="stylesheet" href="https://fonts.googleapis.com/css2?family=Noticia+Text:wght@400;700&family=Vollkorn:wght@400&display=swap">
<style>
  :root {
    --ink: #3d3d3d;
    --accent: #f0a531;
    --pink: #e54298;
    --slate: #545553;
    --yellow: #fed31c;
    --footer: #3a3a3a;
    --white: #ffffff;
    --photo-warm: #c8873c;
  }
  * { margin: 0; padding: 0; box-sizing: border-box; }
  html, body { width: 1200px; height: 929px; overflow: hidden; background: var(--white); }
  body { font-family: "Noticia Text", Georgia, serif; color: var(--ink); }
  .page { position: relative; width: 1200px; height: 929px; }

  .site-header {
    position: absolute; left: 0; top: 0; width: 1200px; height: 103px;
    background: linear-gradient(#ffffff, #f1f1f1);
  }
  .brand {
    position: absolute; left: 74px; top: 16px;
    font-family: "Vollkorn", Georgia, serif; font-size: 64px; line-height: 1; color: var(--ink);
  }
  .main-nav { position: absolute; top: 54px; left: 0; width: 1200px; }
  .main-nav a {
    position: absolute; font-size: 17px; color: var(--ink); text-decoration: none; white-space: nowrap;
  }
  .main-nav a.is-current { color: var(--accent); }
  .main-nav a.is-current::after {
    content: ""; position: absolute; left: -7px; right: -6px; top: 27px; height: 2px; background: var(--accent);
  }

  .tile { position: absolute; top: 148px; width: 339px; height: 321px; }
  .tile-photo { left: 75px; background: radial-gradient(circle at 50% 50%, #d9a35e, var(--photo-warm) 60%, #9b6530); }
  .tile-help { left: 431px; background: var(--pink); color: var(--white); }
  .tile-help .arrow { position: absolute; left: 28px; top: 44px; }
  .tile-help h2 { position: absolute; left: 55px; top: 32px; font-weight: 400; font-size: 32px; line-height: 1.1; }
  .tile-help p { position: absolute; left: 55px; top: 72px; font-size: 24px; }
  .tile-leader { left: 787px; background: var(--slate); color: var(--white); text-align: right; padding: 36px 28px 0 20px; }
  .tile-leader h2 { font-weight: 400; font-size: 24px; margin-bottom: 14px; padding-right: 0; }
  .tile-leader p { font-size: 14.5px; line-height: 25px; padding-right: 2px; }

  .intro { position: absolute; left: 75px; top: 533px; width: 662px; }
  .intro h1 { font-weight: 400; font-size: 25px; letter-spacing: 0.5px; line-height: 1.2; }
  .intro h3 { font-weight: 400; font-size: 20.5px; letter-spacing: 0.5px; margin-top: 4px; }
  .intro .body { margin-top: 18px; font-size: 14.5px; line-height: 22px; letter-spacing: 0.35px; text-align: justify; }
  .intro .kickstart { margin-top: 24px; font-size: 13.5px; }
  .intro .kickstart a { font-size: 18px; color: #111; text-decoration: none; }

  .signup { position: absolute; left: 794px; top: 601px; width: 333px; height: 148px; background: var(--yellow); }
  .signup .badge { position: absolute; left: 20px; top: 15px; width: 70px; height: 70px; border-radius: 50%; background: #3b3b3b; }
  .signup .badge-shadow { position: absolute; left: 14px; top: 100px; width: 82px; height: 6px; border-radius: 50%; background: rgba(0,0,0,0.12); }
  .signup label { position: absolute; left: 114px; top: 28px; width: 200px; font-size: 15.5px; line-height: 22px; color: #2d2d2d; }
  .signup .field { position: absolute; left: 114px; top: 86px; width: 159px; height: 37px; border: 0; background: var(--white); padding-left: 16px; font: 13.5px Arial, sans-serif; color: #888; }
  .signup .send { position: absolute; left: 273px; top: 86px; width: 38px; height: 37px; background: var(--accent); border: 0; display: flex; align-items: center; justify-content: center; }

  .site-footer { position: absolute; left: 0; top: 838px; width: 1200px; height: 91px; background: var(--footer); color: var(--white); font-size: 14.5px; }
  .site-footer .legal { position: absolute; left: 76px; top: 26px; }
  .site-footer .contact { position: absolute; left: 76px; top: 54px; word-spacing: 1px; }
  .site-footer .contact span + span { margin-left: 26px; }
  .social { position: absolute; top: 27px; left: 969px; display: flex; gap: 10px; list-style: none; }
  .social li { width: 31px; height: 31px; border-radius: 2px; }
  .social .s1 { background: #1da1f2; }
  .social .s2 { background: #3b5998; }
  .social .s3 { background: #d34836; }
  .social .s4 { background: #3f729b; }
</style>
</head>
<body>
<div class="page">
  <header class="site-header">
    <div class="brand">Halvik.</div>
    <nav class="main-nav">
      <a href="#" style="left:685px">Home</a>
      <a href="#" style="left:783px">What H do</a>
      <a href="#" style="left:929px">Who H are</a>
      <a href="#" class="is-current" style="left:1067px">Why H</a>
    </nav>
  </header>

  <div class="tile tile-photo" role="img" aria-label="Photo from above of a man slumped face-down on a cluttered wooden breakfast table"></div>

  <section class="tile tile-help">
    <svg class="arrow" width="12" height="20" viewBox="0 0 12 20"><path d="M0 0 L12 10 L0 20 Z" fill="#ffffff"/></svg>
    <h2>Stuck?</h2>
    <p>Help for hire..</p>
  </section>

  <section class="tile tile-leader">
    <h2>Passenger vs leader</h2>
    <p>Experiencing quite the opposite of leading? You might be lacking the right tools to identify the structural needs of a growing business - or missing the momentum to shape it.</p>
  </section>

  <section class="intro">
    <h1>YOU GOT YOUR ACT TOGETHER?</h1>
    <h3>CONGRATULATIONS.</h3>
    <p class="body">Actually, many businesses don’t. Many business leaders instead feel uneasy when thinking about the Big Picture; the company’s strategic framework.&nbsp; Or how it is relayed internally to employees.<br>The list of complex issues in need of attention keeps growing but simply not enough time. As everyday business need to be prioritized to stay ahead, it can certainly be a hardship to even identify, yet perform the structural improvements needed to mature with your industry.</p>
    <p class="kickstart">Start by downloading Halvik's <a href="#">Kickstart offer [SWE].</a></p>
  </section>

  <form class="signup">
    <div class="badge" role="img" aria-label="Dark speech-bubble badge with hand-lettered 'Get in touch'"></div>
    <div class="badge-shadow"></div>
    <label for="email">Simply drop your Email here...</label>
    <input class="field" id="email" type="text" placeholder="Enter Email">
    <button class="send" type="button" aria-label="Send">
      <svg width="10" height="14" viewBox="0 0 10 14"><path d="M2 1 L8 7 L2 13" stroke="#ffffff" stroke-width="2.6" fill="none"/></svg>
    </button>
  </form>

  <footer class="site-footer">
    <div class="legal">Halvik © 2015 | Privacy Policy</div>
    <div class="contact"><span>T: +46 [0] 700 12 34 56</span><span>E: info@halvik-demo.se</span></div>
    <ul class="social">
      <li class="s1"></li><li class="s2"></li><li class="s3"></li><li class="s4"></li>
    </ul>
  </footer>
</div>
</body>
</html>
```